A clean crisp business card for a Landscape Construction company. Designed to be easy to read contact/ info and also be appealing/interesting, unlike a traditional business card.

Industry/Entity Type

Landscape Construction

Contact Information for Business Card

Company name : Brambleford Landscape Construction, phone number: (877) 62Vista, website:Bramblefordyards.example, Email, sales@bramblefordyards.example

Requirements
Nice to have
• Luxurious finishes/ details…. Icons or emblems next to contact info
Should not have
• Clipart or general pictures

```html
<!DOCTYPE html>
<html lang="en">
<head>
<meta charset="utf-8">
<title>Brambleford Landscape Construction – Business Card</title>
<link rel="stylesheet" href="https://fonts.googleapis.com/css2?family=Cinzel:wght@500&family=Teko:wght@500&family=Montserrat:wght@600&family=Source+Sans+3:wght@400&display=swap">
<style>
  :root {
    --page: #f1f1f1;
    --card-dark: #000000;
    --card-light: #ffffff;
    --ink: #111111;
    --brand-green: #9cc13a;
    --icon-bg: #000000;
    --icon-fg: #ffffff;
  }
  * { margin: 0; padding: 0; box-sizing: border-box; }
  html, body {
    width: 1200px; height: 1200px; overflow: hidden;
    background: var(--page);
  }
  .canvas { position: relative; width: 1200px; height: 1200px; }

  .card {
    position: absolute; left: 203px; width: 794px; height: 453px;
    border-radius: 46px; overflow: hidden;
  }
  .card--front { top: 103px; background: var(--card-dark); }
  .card--back  { top: 645px; background: var(--card-light); }

  .mosaic { position: absolute; top: 0; height: 100%; }
  .card--front .mosaic {
    left: 495px; width: 236px;
    background: linear-gradient(180deg,
      #3a2a08 0%, #e88a10 8%, #6a8a2a 20%, #2a2a2a 30%,
      #e07a10 38%, #b01020 48%, #7a7a7a 58%, #c01a2a 68%,
      #e0a010 78%, #1a5aa0 90%, #3a3a3a 100%);
    opacity: .85;
  }
  .card--back .mosaic {
    left: 521px; width: 198px;
    background: linear-gradient(180deg,
      #fbd9a0 0%, #f7b24a 10%, #c9dd9a 22%, #f4f4f4 32%,
      #f6b07a 40%, #f29aa0 52%, #9fbfe6 62%, #f7a0a8 72%,
      #b8d0ee 82%, #f8c27a 100%);
    opacity: .75;
  }
  .card--back .fold {
    position: absolute; left: 436px; top: 40px; width: 18px; height: 380px;
    background: linear-gradient(90deg, rgba(0,0,0,0), rgba(0,0,0,.06));
  }

  .brand {
    position: absolute; left: 6px; top: 186px; width: 430px;
    display: flex; flex-direction: column; align-items: center;
    font-family: "Cinzel", Georgia, serif; font-weight: 500;
    color: var(--brand-green);
  }
  .brand__mark {
    width: 30px; height: 30px; border-radius: 50%;
    background: var(--brand-green); margin-bottom: 18px;
  }
  .brand__name { font-size: 50px; line-height: 1; letter-spacing: 1px; }
  .brand__sub  { font-size: 18px; letter-spacing: 4.4px; margin-top: 10px; }

  .person { position: absolute; left: 82px; top: 82px; color: var(--ink); }
  .person__name {
    font-family: "Teko", "Arial Narrow", sans-serif; font-weight: 500;
    font-size: 62px; line-height: 1; letter-spacing: 1.5px;
  }
  .person__role {
    font-family: "Montserrat", Arial, sans-serif; font-weight: 600;
    font-size: 21px; margin-top: -5px; letter-spacing: 1px;
  }

  .contacts {
    position: absolute; left: 83px; top: 228px; list-style: none;
    font-family: "Source Sans 3", Arial, sans-serif; font-size: 16px;
    color: var(--ink);
  }
  .contacts li { display: flex; align-items: center; height: 24px; margin-bottom: 10px; }
  .contacts li.contacts__web { margin-top: 16px; }
  .contacts__icon {
    width: 24px; height: 24px; background: var(--icon-bg);
    display: flex; align-items: center; justify-content: center;
    margin-right: 16px; flex: none;
  }
  .contacts__icon svg { width: 15px; height: 15px; fill: var(--icon-fg); }
</style>
</head>
<body>
<main class="canvas">

  <section class="card card--front" aria-label="Card front">
    <div class="brand">
      <span class="brand__mark" aria-hidden="true"></span>
      <span class="brand__name">Brambleford</span>
      <span class="brand__sub">LANDSCAPE CONSTRUCTION</span>
    </div>
    <div class="mosaic" role="img" aria-label="Column of multicoloured overlapping squares"></div>
  </section>

  <section class="card card--back" aria-label="Card back">
    <div class="person">
      <h1 class="person__name">YOUR NAME</h1>
      <p class="person__role">Graphic Designer</p>
    </div>

    <ul class="contacts">
      <li>
        <span class="contacts__icon"><svg viewBox="0 0 16 16"><path d="M8 1a5 5 0 0 0-5 5c0 3.6 5 9 5 9s5-5.4 5-9a5 5 0 0 0-5-5zm0 7a2 2 0 1 1 0-4 2 2 0 0 1 0 4z"/></svg></span>
        1420 Orchard Hollow Rd., Suite 204, Fairbrook, OH 45000
      </li>
      <li>
        <span class="contacts__icon"><svg viewBox="0 0 16 16"><path d="M4 1l2.5 3-1.6 1.8a9 9 0 0 0 5.3 5.3L12 9.5l3 2.5-1.5 2.5C7.5 15 1 8.5 1.5 2.5z"/></svg></span>
        (555) 555 0162
      </li>
      <li>
        <span class="contacts__icon"><svg viewBox="0 0 16 16"><path d="M1 3h14v10H1zm1.5 1.2V5l5.5 4 5.5-4v-.8zM2.5 6.6V12h11V6.6L8 10.6z"/></svg></span>
        sales@bramblefordyards.example
      </li>
      <li class="contacts__web">
        <span class="contacts__icon"><svg viewBox="0 0 16 16"><path d="M3 1l10 7-4.3.8 2.6 5-1.8.9-2.6-5L3 13z"/></svg></span>
        bramblefordyards.example
      </li>
    </ul>

    <div class="fold" aria-hidden="true"></div>
    <div class="mosaic" role="img" aria-label="Column of soft multicoloured squares"></div>
  </section>

</main>
</body>
</html>
```